Banner & also another minor digital image for an Online Academic Journal

A direct example of what I need can be found in this webpage: http://openfolio.kestrelvale.edu/qrmt/
(Please see attached files, "sAMPLE", and "sAMPLE 2", so you can see what I mean.)
This link (http://openfolio.kestrelvale.edu/qrmt/) is for an existing ONLINE ACADEMIC JOURNAL at the Harrowgate Institute of Letters.
It will help for you to be acquainted with the format of Online Academic Journals.
You will find that there is a banner on top as well as a digital image of a journal/book cover on the right.
I need a
(1) banner and
a (2) digital journal/book cover
for a website for an ONLINE ACADEMIC JOURNAL.
I am looking for a serious, professional, elegant design.
There will not be a print version. Only web-based online publication. No coding needed, only PSD, JPG/PNG and PDF.
1) We use QuillNest (http://openfolio.quillnest.com/archive-platform/periodicals/) for the digital image of the journal/book cover layout. Link shows the general layout of the journal website.
2) For the digital image of the journal/book cover and also the banner,
Name of the journal is....
"Solace: A Review on Coercion and Abuse Studies"
Only this text will be used and applied to both banner and cover.
***The color associated with the theme of dignity is purple
****You could also add the color red.
*****I don't want the design to be garish, but accents in red might represent
the sexual exploitation and violence in the title.
3) Attached "sAmple 2" file is a basic design for the digital image of the journal/book cover from QuillNest. I am looking for something more elegant and professional looking. Your creativity is encouraged. I am open to receiving your interpretation.
Target Market(s)
Academics & Community Professionals
Industry/Entity Type
Non Profit
Match journal design

```html
<!DOCTYPE html>
<html lang="en">
<head>
<meta charset="utf-8">
<title>Solace: A Review on Coercion and Abuse Studies — Banner and Cover</title>
<link rel="stylesheet" href="https://fonts.googleapis.com/css2?family=Cormorant+SC:wght@500;600&display=swap">
<style>
  :root {
    --stage-light: #a7a4b6;
    --stage-dark: #625d78;
    --violet-deep: #2a0538;
    --violet-mid: #5a1480;
    --violet-bright: #9b3fd6;
    --violet-glow: #c27df0;
    --plum-band: #470f58;
    --ink-light: #ffffff;
    --rule: rgba(255, 255, 255, 0.85);
  }
  * { margin: 0; padding: 0; box-sizing: border-box; }
  html, body { width: 1200px; height: 600px; overflow: hidden; }
  body {
    position: relative;
    background: radial-gradient(ellipse at 50% 30%, var(--stage-light) 0%, var(--stage-dark) 100%);
    font-family: "Cormorant SC", "Times New Roman", serif;
    color: var(--ink-light);
  }

  /* Web banner */
  .banner {
    position: absolute;
    left: 10px; top: 53px;
    width: 1180px; height: 139px;
    overflow: hidden;
    box-shadow: 0 2px 6px rgba(0, 0, 0, 0.35);
  }
  .banner-backdrop {
    position: absolute; inset: 0;
    background:
      radial-gradient(ellipse 30% 40% at 62% 30%, rgba(194, 125, 240, 0.55), transparent 70%),
      radial-gradient(ellipse 40% 25% at 85% 70%, rgba(194, 125, 240, 0.45), transparent 70%),
      linear-gradient(180deg, var(--violet-mid) 0%, var(--violet-bright) 35%, var(--violet-deep) 60%, var(--violet-mid) 80%, var(--violet-deep) 100%);
  }
  .banner-title {
    position: absolute;
    left: 98px; top: 74px;
    font-size: 76px; font-weight: 600;
    line-height: 1; letter-spacing: 1px;
  }
  .banner-rule {
    position: absolute;
    left: 0; top: 160px;
    width: 480px; height: 2px;
    background: linear-gradient(90deg, var(--rule) 0%, var(--rule) 80%, transparent 100%);
  }
  .banner-subtitle {
    position: absolute;
    left: 892px; top: 36px;
    font-size: 22px; font-weight: 500;
    line-height: 23px; letter-spacing: 0.5px;
  }

  /* Journal cover */
  .cover {
    position: absolute;
    left: 474px; top: 214px;
    width: 251px; height: 362px;
    overflow: hidden;
    box-shadow: 0 2px 6px rgba(0, 0, 0, 0.35);
  }
  .cover-backdrop {
    position: absolute; left: 0; top: 0;
    width: 100%; height: 230px;
    background:
      radial-gradient(ellipse 60% 20% at 55% 10%, rgba(194, 125, 240, 0.6), transparent 70%),
      radial-gradient(ellipse 70% 15% at 40% 75%, rgba(194, 125, 240, 0.55), transparent 70%),
      linear-gradient(180deg, var(--violet-mid) 0%, var(--violet-bright) 18%, var(--violet-deep) 45%, var(--violet-mid) 62%, var(--violet-bright) 75%, var(--violet-deep) 100%);
  }
  .cover-title {
    position: absolute;
    left: 31px; top: 48px;
    font-size: 34px; font-weight: 600;
    line-height: 1; letter-spacing: 0.5px;
  }
  .cover-rule {
    position: absolute;
    left: 0; top: 229px;
    width: 100%; height: 2px;
    background: var(--rule);
  }
  .cover-band {
    position: absolute;
    left: 0; top: 231px;
    width: 100%; height: 131px;
    background: var(--plum-band);
  }
  .cover-subtitle {
    position: absolute;
    left: 31px; top: 26px;
    font-size: 18px; font-weight: 500;
    line-height: 19px; letter-spacing: 0.3px;
  }
</style>
</head>
<body>
  <header class="banner">
    <div class="banner-backdrop" role="img" aria-label="Flowing violet silk waves"></div>
    <h1 class="banner-title">Solace</h1>
    <div class="banner-rule"></div>
    <p class="banner-subtitle">A Review on<br>Coercion and Abuse<br>Studies</p>
  </header>

  <section class="cover">
    <div class="cover-backdrop" role="img" aria-label="Flowing violet silk waves"></div>
    <h2 class="cover-title">Solace</h2>
    <div class="cover-rule"></div>
    <div class="cover-band">
      <p class="cover-subtitle">A Review on<br>Coercion and Abuse<br>Studies</p>
    </div>
  </section>
</body>
</html>
```